Private Investment Firm Needs PowerPoint Presentation Template

Design PowerPoint template, take Pinebrook-submitted rough presentation draft, and drop it into new template. See attached Project Brief file for more detail.
Updates

Some decent designs have been submitted but they seem to lack the understanding of our target markets. I am hopeful that more time and feedback will result in better results.

Target Market(s)

Private company owners and intermediaries.

Font styles to use
Serif

Colors
3176b5

Requirements
Must have
• See attached Project Brief.
Nice to have
Should not have
• No B2C fluff--this is a B2B project.

```html
<!DOCTYPE html>
<html lang="en">
<head>
<meta charset="UTF-8">
<title>Pinebrook Capital – What Is Non-Control Capital?</title>
<link href="https://fonts.googleapis.com/css2?family=Figtree:wght@400;600;700&family=Libre+Baskerville&display=swap" rel="stylesheet">
<style>
  :root {
    --brand-blue: #0a70c4;
    --ink: #1c1c1c;
    --paper: #ffffff;
    --sky-light: #e9eef1;
    --sky-mid: #c4d0d6;
    --glass: #8fa6b1;
  }
  html, body {
    margin: 0;
    padding: 0;
    overflow: hidden;
    background: var(--paper);
  }
  .slide {
    position: relative;
    width: 1200px;
    height: 676px;
    overflow: hidden;
    background: var(--paper);
    font-family: "Figtree", sans-serif;
    color: var(--ink);
  }
  .side-band {
    position: absolute;
    top: 0;
    left: 0;
    width: 44px;
    height: 100%;
    background: var(--brand-blue);
  }
  .side-band__url {
    position: absolute;
    left: 22px;
    top: 336px;
    transform: translate(-50%, -50%) rotate(-90deg);
    white-space: nowrap;
    font-family: "Libre Baskerville", serif;
    font-size: 14px;
    color: var(--paper);
    letter-spacing: 0.2px;
  }
  .edge-band {
    position: absolute;
    top: 0;
    right: 0;
    width: 12px;
    height: 100%;
    background: var(--brand-blue);
  }
  .hero-photo {
    position: absolute;
    top: 0;
    left: 560px;
    width: 628px;
    height: 100%;
    background:
      linear-gradient(60deg, transparent 55%, var(--glass) 56%, #6f8894 100%),
      linear-gradient(90deg, var(--paper) 0%, var(--sky-light) 35%, var(--sky-mid) 100%);
  }
  .page-number {
    position: absolute;
    top: 18px;
    right: 30px;
    font-family: "Libre Baskerville", serif;
    font-size: 17px;
    color: var(--ink);
  }
  .slide-title {
    position: absolute;
    top: 80px;
    left: 86px;
    margin: 0;
    font-size: 29px;
    font-weight: 700;
    color: var(--brand-blue);
    letter-spacing: 0.2px;
  }
  .points {
    position: absolute;
    top: 145px;
    left: 86px;
    width: 620px;
    margin: 0;
    padding: 0;
    list-style: none;
  }
  .points__item {
    position: relative;
    padding-left: 28px;
    margin-bottom: 28px;
    font-size: 17.5px;
    line-height: 28px;
    letter-spacing: 0.2px;
  }
  .points__item::before {
    content: "";
    position: absolute;
    left: 0;
    top: 7px;
    width: 13px;
    height: 13px;
    background: var(--brand-blue);
  }
  .brand {
    position: absolute;
    left: 68px;
    bottom: 24px;
    display: flex;
    align-items: center;
    gap: 10px;
  }
  .brand__dot {
    width: 34px;
    height: 34px;
    border-radius: 50%;
    background: var(--brand-blue);
  }
  .brand__name {
    font-size: 19px;
    font-weight: 600;
    color: var(--brand-blue);
    letter-spacing: 1px;
  }
</style>
</head>
<body>
  <main class="slide">
    <div class="hero-photo" role="img" aria-label="Upward view of a glass office tower against a pale sky"></div>
    <aside class="side-band">
      <span class="side-band__url">www.pinebrookcapital.com</span>
    </aside>
    <div class="edge-band"></div>
    <span class="page-number">3</span>

    <h1 class="slide-title">WHAT IS NON-CONTROL CAPITAL?</h1>
    <ul class="points">
      <li class="points__item">Requires the alignment of management incentives with ownership</li>
      <li class="points__item">In essence, a company receives the capital it needs to implement its business plans but owners continue to retain ultimate control</li>
    </ul>

    <div class="brand">
      <span class="brand__dot"></span>
      <span class="brand__name">PINEBROOK CAPITAL</span>
    </div>
  </main>
</body>
</html>
```